The Quiet Harvest Book Cover

Cover for Multiauthor Ebook & Paper Print Book Cover

Book Title:
The Quiet Harvest: Lessons of Insight From A Circle of Mentors to Guide You Toward a Fuller Journey

This book will offer the wisdom and philosophies of a variety of different coaches to allow future clients to get a taste of you and your style and prepare them to work with you!

A coach does not fix you. Or heal you. They coach you - offer thoughts to ponder, guidance, techniques to try. All to help you plays and succeed at the game of life.

Each coach has their own personality, training, experience, method and philosophy they bring to the table. The underlying purpose is to guide you through the quiet harvest, to become the person you desire and aspire to be. Different coaches for different folks, yet they all have their own unique wisdom and special sauce to share.

This book is a collection of just that. A tasting of the wisdom and philosophies of a variety of different coaches for you to experience.

Types of Coaches: Clarity, Dreams, Goals, Motivation, Mindset,  Subconscious, Beliefs, Behavior, Accountability, Life, Wellness, Love & Dating, Relationships, Sex, Business, Career,  Executive,  Personal Development,  Writing, Wellness, Fitness, Parenting,  Style, Spirituality, Public Speaking, Financial,  Time management, Weight Loss, Running, Self esteem,  Tarot, Astrology, Enneagram, Soul path/ Dharma, Skills, Performance,  Speaking / Communication, Leadership, Shadow Work, Acting, Sports, ANY & ALL

Target Market(s)

Males or females looking for guidance and words of wisdom from an expert coach - maybe to find one that resonates with them to work with further. Ages 16 and up. Any Gender. International. Looking to improve their life!

Industry/Entity Type

Self Development, Wellness, Coaching, Personal Growth, Fitness, Spirituality, Business, Relationships

Font styles to use
Serif
Script

Colors
0054AA
0677BA
7BADD7
CADEEF
E8F1F8
FFF300
FFF600
FEFA6F
FFFEC7
FFFEE8

Requirements
Must have
• I am looking for a visually appealing, unique cover that encompasses the breadth and depth of the transformation that people can go through and inspires them to want to grow and change even more. I love when elegant and classic simplicity is combined with some kind of twist that catches the eye and provokes thought. I love complimentary fonts, colors, design elements. You can visit my Brindlemart Author Page - Dr. Marisol Pendergast Voyle to see my titles to see what I have liked! But I am also excited to see where you can make my vision even better!!
Nice to have
• Front Cover - Image, Title and Subtitle, The Lantern Publishing House, Spine - Title and Publishing House Logo, Back - Book Blurb, Authors Names, Info about Publishing House, ISBN Barcode
Should not have
• Anything too feminine or too masculine as I want to encourage coaches of all genders to participate.

```html
<!DOCTYPE html>
<html lang="en">
<head>
<meta charset="utf-8">
<title>The Quiet Harvest – Book Cover</title>
<link rel="stylesheet" href="https://fonts.googleapis.com/css2?family=Rubik:wght@700;800&family=Roboto+Condensed:ital,wght@0,700;1,700&display=swap">
<style>
  :root {
    --page-bg: #eceef1;
    --cover-top: #f4f1f8;
    --cover-bottom: #c9dcef;
    --ring-blue: #d8ecf7;
    --glow-white: #ffffff;
    --title-grey: #555558;
    --subtitle-grey: #5d5d60;
    --publisher-navy: #27306e;
    --wing-red: #e0525a;
    --wing-purple: #8a79bf;
    --wing-teal: #1fa9a8;
  }
  * { margin: 0; padding: 0; box-sizing: border-box; }
  html, body { width: 1036px; height: 1200px; overflow: hidden; }
  body {
    background: var(--page-bg);
    display: flex;
    align-items: center;
    justify-content: center;
  }
  .book-cover {
    position: relative;
    width: 800px;
    height: 1140px;
    background: linear-gradient(180deg, var(--cover-top) 0%, #eef1f8 55%, var(--cover-bottom) 100%);
    overflow: hidden;
    box-shadow: 0 6px 24px rgba(0,0,0,0.12);
  }
  .cover-art { position: absolute; inset: 0; }
  .cover-text {
    position: absolute;
    left: 0; right: 0;
    top: 430px;
    text-align: center;
  }
  .book-title {
    font-family: "Rubik", sans-serif;
    font-weight: 800;
    color: var(--title-grey);
    font-size: 92px;
    line-height: 0.98;
    letter-spacing: -1px;
  }
  .book-subtitle {
    margin: 34px auto 0;
    width: 470px;
    font-family: "Roboto Condensed", sans-serif;
    font-style: italic;
    font-weight: 700;
    color: var(--subtitle-grey);
    font-size: 30px;
    line-height: 1.2;
  }
  .publisher {
    position: absolute;
    left: 0; right: 0;
    bottom: 70px;
    text-align: center;
    font-family: "Roboto Condensed", sans-serif;
    font-weight: 700;
    color: var(--publisher-navy);
    font-size: 40px;
    letter-spacing: 0.5px;
  }
</style>
</head>
<body>
  <main class="book-cover">
    <svg class="cover-art" width="800" height="1140" viewBox="0 0 800 1140">
      <defs>
        <radialGradient id="centre-glow" cx="50%" cy="50%" r="50%">
          <stop offset="0%" stop-color="var(--glow-white)"/>
          <stop offset="78%" stop-color="var(--glow-white)"/>
          <stop offset="100%" stop-color="var(--ring-blue)"/>
        </radialGradient>
        <linearGradient id="wing-band-top" x1="0" y1="0" x2="1" y2="1">
          <stop offset="0%" stop-color="var(--wing-red)"/>
          <stop offset="40%" stop-color="var(--wing-purple)"/>
          <stop offset="70%" stop-color="var(--wing-teal)"/>
          <stop offset="100%" stop-color="var(--wing-red)"/>
        </linearGradient>
        <linearGradient id="wing-band-bottom" x1="0" y1="0" x2="1" y2="0">
          <stop offset="0%" stop-color="var(--wing-purple)"/>
          <stop offset="50%" stop-color="var(--wing-teal)"/>
          <stop offset="100%" stop-color="var(--wing-red)"/>
        </linearGradient>
      </defs>
      <circle class="outer-ring" cx="400" cy="560" r="420" fill="var(--ring-blue)" opacity="0.55"/>
      <circle class="centre-glow" cx="410" cy="560" r="350" fill="url(#centre-glow)"/>
      <path class="swirl-line" d="M120 620 A330 330 0 0 1 520 250" fill="none" stroke="#cfe6f4" stroke-width="14" stroke-linecap="round"/>
      <path class="butterfly-swirl" role="img" aria-label="Swirl of butterfly silhouettes in red, purple and teal rising around the circle"
            d="M0 0 H800 V760 C760 700 740 560 700 430 C640 260 460 170 260 200 C150 215 60 230 0 260 Z"
            fill="url(#wing-band-top)" opacity="0.35"/>
      <path class="butterfly-trail" role="img" aria-label="Trail of smaller butterfly silhouettes along the bottom of the circle"
            d="M150 900 C300 860 500 860 680 800 L700 880 C520 960 320 990 170 960 Z"
            fill="url(#wing-band-bottom)" opacity="0.3"/>
    </svg>

    <section class="cover-text">
      <h1 class="book-title">The<br>Quiet<br>Harvest</h1>
      <p class="book-subtitle">Lessons of Insight From A Circle of Mentors to Guide You Toward a Fuller Journey</p>
    </section>

    <p class="publisher">THE LANTERN PUBLISHING HOUSE</p>
  </main>
</body>
</html>
```